Moon Tot needs ecommerce website design help

We need someone to set up a fully functional website for us. We sell baby bibs, I attached them along with our company logo (MTG: moon tot goods). The bibs are made of 100% silicon, they are safe, light weight, soft, smooth, flexible, dishwasher safe and has funny faces.

Business name: Moon Tot Goods
Elm Hollow, NY 00000
email: MoonTotGoods@mailbox-example.com
tel.: (555) 014-TOTS
website: MoonTotGoods-example.com

Target Market(s)

18-40

Industry/Entity Type

Baby

Coding

Coded - Design and coding required

Number of Pages Required

5+ page

Requirements
Must have
• 1. Pages: Why buy from us, Contact Us, Home page, Products Page, Blog
• 2. Use the colors from our logo for the web design.
• 3. Need a link that will connect visitors to our facebook, instagram, Pinterest and Tumblr account. Would like links on,the top left side of the page
Nice to have
• My Cart page
• 1. On contact us page, we want to include some type of template for the customer to complete. (Ex: name, email address, contact number, optional home address, comments)
• 2. When clients visit our website, we want a capture/pop up for the customer to subscribe to our email list to receive discounts. (Ex. Want 10% off your next order ? Suscribe to our mailing list below and get a 10% off code to use at check out. If they don't want to subscribe, they have the option to select "No Thank You, I want to pay full price).
• 3. On home page have subscribe to our email list.

```html
<!DOCTYPE html>
<html lang="en">
<head>
<meta charset="utf-8">
<title>Moon Tot Goods</title>
<link href="https://fonts.googleapis.com/css2?family=Roboto:wght@300;400;500;700&family=Roboto+Slab:wght@300;400&family=Lato:ital,wght@1,400&family=Niconne&display=swap" rel="stylesheet">
<style>
:root{
  --red:#ec4a60;
  --orange:#e9a53a;
  --green:#8cc63f;
  --ink:#3a3a3a;
  --muted:#7a7a7a;
  --page:#f7f7f7;
  --backdrop:#e4eaee;
  --footer:#2a2623;
  --footer-text:#b9b4ae;
}
*{box-sizing:border-box;margin:0;padding:0}
html,body{width:787px;height:1200px;overflow:hidden}
body{background:var(--backdrop);font-family:'Roboto',sans-serif;color:var(--ink);position:relative}
.abs{position:absolute}
.page{position:absolute;left:39px;top:19px;width:709px;height:1157px;background:var(--page)}
.brand{left:50px;top:42px;display:flex;align-items:center;gap:8px}
.brand .dot{width:40px;height:40px;border-radius:50%;background:var(--red)}
.brand .name{font:700 34px 'Roboto',sans-serif;color:var(--green);letter-spacing:1px}
.welcome{right:175px;top:52px;font-size:9px;color:var(--red)}
.account-links{right:175px;top:66px;font-size:7.5px;color:var(--muted)}
.cart-icon{left:642px;top:46px}
.cart-title{left:677px;top:50px;font-size:9px;color:var(--green)}
.cart-count{left:677px;top:65px;font-size:7.5px;color:var(--muted)}
.nav{left:48px;top:104px;width:526px;height:30px;border-bottom:1.5px solid #444}
.nav a{position:absolute;top:11px;font-size:8px;color:var(--ink);text-decoration:none;font-weight:500}
.nav .active{color:var(--red)}
.nav .bar{position:absolute;left:0;top:-1px;width:66px;height:2px;background:var(--red)}
.search{left:574px;top:104px;width:135px;height:30px;border-bottom:1.5px solid #444;font:italic 8px 'Roboto',sans-serif;color:#aaa;padding:12px 10px}
.search-btn{left:709px;top:104px;width:29px;height:30px;background:var(--orange)}
.cats{left:48px;top:150px;width:217px}
.cat{height:67px;border-bottom:1px solid #e2e2e2;text-align:center;padding-top:20px}
.cat h3{font:400 17px 'Roboto',sans-serif;color:#555}
.cat p{font-size:8px;color:var(--red);margin-top:3px}
.hero{left:265px;top:150px;width:473px;height:274px;background:linear-gradient(90deg,#e6dedd,#f1eeee 60%,#e9e6e3)}
.hero-stripe{left:290px;top:150px;width:12px;height:274px;background:#e56a78}
.shop-now{left:265px;top:366px;width:207px;height:25px;background:rgba(226,92,108,.75);font:24px 'Niconne',cursive;color:#fbe4e7;text-align:center;line-height:25px}
.section-title{left:50px;top:452px;font:24px 'Niconne',cursive;color:var(--green)}
.section-rule{left:48px;top:476px;width:690px;height:1px;background:#c9c29a}
.arrow{width:17px;height:17px;border-radius:50%;top:452px}
.card{top:492px;width:150px;height:248px;text-align:center}
.card.boxed{border:1px solid #e3e3e3}
.bib{position:absolute;left:28px;top:14px;width:94px;height:118px;border-radius:45% 45% 40% 40%}
.rating{position:absolute;left:0;right:0;top:146px;font-size:8px;color:var(--orange)}
.rating span{color:#999;margin-left:10px;font-size:7px}
.pname{position:absolute;left:0;right:0;top:164px;font:400 11px 'Roboto Slab',serif;color:#444}
.price{position:absolute;left:0;right:0;top:180px;font:700 14px 'Roboto',sans-serif;color:var(--orange)}
.actions{position:absolute;left:24px;top:210px;display:flex;border:1px solid #ddd;background:#fff;height:22px}
.actions div{font-size:7.5px;line-height:20px;padding:0 8px;border-right:1px solid #ddd;color:#444}
.actions div:last-child{border:0}
.about-title{left:53px;top:794px;font:400 14.5px 'Roboto',sans-serif;color:#333}
.about-lead{left:53px;top:822px;width:440px;font:italic 9.5px/14px 'Roboto',sans-serif;color:var(--orange)}
.about-body{left:53px;top:862px;width:450px;font:8px/14.5px 'Roboto',sans-serif;color:#666}
.vrule{left:509px;top:822px;width:1px;height:86px;background:#e2e2e2}
.events-title{left:524px;top:794px;font:400 14.5px 'Roboto',sans-serif;color:#333}
.event{left:525px;width:208px;height:34px;border-bottom:1px solid #e6e6e6;font-size:8px;color:#777;display:flex;align-items:center;gap:8px}
.event b{font-weight:400;color:var(--orange);font-size:9px}
.event i{width:11px;height:9px;background:var(--orange);border-radius:2px;flex:none}
.footer{left:39px;top:964px;width:709px;height:212px;background:var(--footer)}
.footer-heading{position:absolute;font:400 10.5px/12px 'Roboto',sans-serif;color:var(--orange);letter-spacing:.3px;white-space:nowrap}
.links{left:62px;top:1019px;list-style:none;font-size:8.5px;line-height:18.3px;color:var(--footer-text)}
.links li::before{content:"";display:inline-block;width:3px;height:3px;border-radius:50%;background:var(--orange);margin:0 12px 2px 2px}
.email-field{left:200px;top:1022px;width:159px;height:24px;background:#f2f2f2;border:1px solid #ccc;font:italic 8px 'Roboto',sans-serif;color:#888;padding:7px 11px}
.send{left:301px;top:1054px;width:58px;height:23px;background:var(--orange);color:#f6d7a5;font-size:8px;text-align:center;line-height:23px}
.contact{left:439px;top:1017px;font-size:8px;line-height:13.5px;color:var(--footer-text)}
.contact a{color:var(--orange);text-decoration:none}
.social{top:1018px;width:25px;height:25px;border-radius:50%;border:2px solid #d9d4ce}
.card-pay{top:1093px;width:22px;height:14px;border-radius:2px}
.copyright{left:39px;top:1148px;width:709px;text-align:center;font-size:8px;color:var(--footer-text)}
.footer-rule{left:39px;top:1132px;width:709px;height:1px;background:#3a3531}
.dim{left:0;top:0;width:787px;height:1200px;background:rgba(60,60,60,.07)}
.popup{left:115px;top:162px;width:553px;height:205px;background:#f8f8f8;box-shadow:0 2px 12px rgba(0,0,0,.15)}
.popup-title{left:20px;top:28px;font:26px 'Niconne',cursive;color:var(--green);white-space:nowrap}
.popup-title strong{font:700 27px 'Roboto',sans-serif}
.popup-text{left:20px;top:73px;font:italic 10.5px/15px 'Lato',sans-serif;color:#333}
.btn{height:26px;font-size:8px;line-height:26px;text-align:center;color:#fff;letter-spacing:.2px}
.btn-decline{left:20px;top:118px;width:209px;background:var(--red)}
.btn-subscribe{left:19px;top:153px;width:104px;background:var(--orange)}
.popup-photo{left:309px;top:0;width:244px;height:205px;background:radial-gradient(ellipse at 55% 45%,#f1ddd1 0%,#ece8e6 45%,#f5f5f5 75%)}
.close{left:654px;top:150px;width:25px;height:25px;border-radius:50%;background:var(--red);border:2px solid #fff;color:#fff;font:700 11px/21px 'Roboto',sans-serif;text-align:center}
</style>
</head>
<body>
<div class="page"></div>

<header>
  <div class="abs brand"><span class="dot"></span><span class="name">MTG</span></div>
  <div class="abs welcome">Welcome to our online store!</div>
  <div class="abs account-links">My Account \ My Wishlist \ My Cart \ Checkout \ Log In</div>
  <svg class="abs cart-icon" width="26" height="34" viewBox="0 0 26 34"><path d="M3 10h20l-2 22H5z" fill="#fff" stroke="#ccc"/><path d="M8 10V6a5 5 0 0 1 10 0v4" fill="none" stroke="#bbb"/></svg>
  <div class="abs cart-title">Shopping Cart</div>
  <div class="abs cart-count">0 Items - $0.00</div>
  <nav class="abs nav">
    <span class="bar"></span>
    <a class="active" style="left:22px">HOME</a>
    <a style="left:82px">PRODUCTS</a>
    <a style="left:163px">WHY BUY FROM US</a>
    <a style="left:282px">BLOG</a>
    <a style="left:342px">CONTACT US</a>
  </nav>
  <div class="abs search">Search here...</div>
  <div class="abs search-btn"><svg width="29" height="30"><circle cx="14" cy="14" r="3.5" fill="none" stroke="#fff" stroke-width="1.3"/><path d="M16.5 16.5l3 3" stroke="#fff" stroke-width="1.3"/></svg></div>
</header>

<section>
  <div class="abs cats">
    <div class="cat"><h3>New Arrivals</h3><p>GET THE LATEST</p></div>
    <div class="cat"><h3>Gift Sets</h3><p>GREAT FOR SHOWERS</p></div>
    <div class="cat"><h3>Free Shipping</h3><p>ON ALL ORDERS</p></div>
    <div class="cat" style="border:0"><h3>Sale Collections</h3><p>GET UP TO 70% OFF</p></div>
  </div>
  <div class="abs hero" role="img" aria-label="Photo of a baby's nursery with a wooden crib"></div>
  <div class="abs hero-stripe"></div>
  <div class="abs shop-now">Shop Now!</div>
</section>

<section>
  <div class="abs section-title">New Products</div>
  <div class="abs section-rule"></div>
  <svg class="abs arrow" style="left:699px" viewBox="0 0 17 17"><circle cx="8.5" cy="8.5" r="8.5" fill="#7ea51e"/><path d="M10 5l-3.5 3.5L10 12" fill="none" stroke="#fff" stroke-width="1.5"/></svg>
  <svg class="abs arrow" style="left:720px" viewBox="0 0 17 17"><circle cx="8.5" cy="8.5" r="8.5" fill="#ececec"/><path d="M7 5l3.5 3.5L7 12" fill="none" stroke="#aaa" stroke-width="1.5"/></svg>

  <div class="abs card boxed" style="left:53px">
    <div class="bib" role="img" aria-label="Pink silicone baby bib with a funny face" style="background:radial-gradient(circle at 50% 60%,#d2348c,#e77ab8)"></div>
    <div class="rating">★★★★☆<span>1 Review(s)</span></div>
    <div class="pname">Lovely - baby bibs</div><div class="price">$34.25</div>
    <div class="actions"><div>Add to Cart</div><div>♡</div><div>🛒︎</div></div>
  </div>
  <div class="abs card" style="left:228px">
    <div class="bib" role="img" aria-label="Blue silicone baby bib with a funny face" style="background:radial-gradient(circle at 50% 60%,#1f7fc9,#5cb2e6)"></div>
    <div class="rating">★★★★☆<span>1 Review(s)</span></div>
    <div class="pname">Lovely - baby bibs</div><div class="price">$34.25</div>
    <div class="actions"><div>Add to Cart</div><div>♡</div><div>🛒︎</div></div>
  </div>
  <div class="abs card" style="left:406px">
    <div class="bib" role="img" aria-label="Green silicone baby bib with a funny face" style="background:radial-gradient(circle at 50% 60%,#63a72a,#9bd25a)"></div>
    <div class="rating">★★★★☆<span>1 Review(s)</span></div>
    <div class="pname">Lovely - baby bibs</div><div class="price">$34.25</div>
    <div class="actions"><div>Add to Cart</div><div>♡</div><div>🛒︎</div></div>
  </div>
  <div class="abs card" style="left:579px">
    <div class="bib" role="img" aria-label="Orange silicone baby bib with a funny face" style="background:radial-gradient(circle at 50% 60%,#e59a12,#f5c24c)"></div>
    <div class="rating">★★★★☆<span>1 Review(s)</span></div>
    <div class="pname">Lovely - baby bibs</div><div class="price">$34.25</div>
    <div class="actions"><div>Add to Cart</div><div>♡</div><div>🛒︎</div></div>
  </div>
</section>

<section>
  <h2 class="abs about-title">About Moon Tot Goods</h2>
  <p class="abs about-lead">we sell baby bibs. The bibs are made of 100% silicon, they are safe, light weight, soft, smooth, flexible, dishwasher safe and has funny faces.</p>
  <p class="abs about-body">Lorem ipsum dolor sit amet conse ctetur adipisicing elit, sed do eiusmod tempor incididunt ut labore et dolore maga aliqua. Ut enim ad minim veniam, quis nostrud exercitation ullamco laboris nisi ut aliquip ex ea commodo consequat Duis aute irure dolor in reprehenderit in voluptate velit esse cillum dolore eu fugia.</p>
  <div class="abs vrule"></div>
  <h2 class="abs events-title">Events</h2>
  <div class="abs event" style="top:814px"><i></i><span><b>Free Home Delivery.</b> Duis aute irure dolor elit</span></div>
  <div class="abs event" style="top:848px"><i></i><span><b>Buy and Save,</b> voluptate velit esse dolore</span></div>
  <div class="abs event" style="top:882px;border:0"><i></i><span><b>Friendly Expert Service.</b> Ut enim ad minim ven</span></div>
</section>

<footer>
  <div class="abs footer"></div>
  <h4 class="footer-heading" style="left:62px;top:994px">USEFUL LINKS</h4>
  <ul class="abs links"><li>Home</li><li>Products</li><li>Why buy from us</li><li>Blog</li><li>Contact us</li></ul>
  <h4 class="footer-heading" style="left:200px;top:994px">NEWSLETTER SUBSCRIPTION</h4>
  <div class="abs email-field">Email Address</div>
  <div class="abs send">SEND</div>
  <h4 class="footer-heading" style="left:439px;top:994px">CONTACT INFO</h4>
  <div class="abs contact">Moon Tot Goods<br>Elm Hollow, NY 00000<br><br>Email: <a>MoonTotGoods@mailbox-example.com</a><br>Tel.: (555) 014-TOTS</div>
  <h4 class="footer-heading" style="left:610px;top:994px">GET SOCIAL</h4>
  <div class="abs social" style="left:609px"></div>
  <div class="abs social" style="left:640px"></div>
  <div class="abs social" style="left:671px"></div>
  <div class="abs social" style="left:702px"></div>
  <h4 class="footer-heading" style="left:610px;top:1072px">PAY THROUGH</h4>
  <div class="abs card-pay" style="left:610px;background:#e8e8ee"></div>
  <div class="abs card-pay" style="left:637px;background:#e98a3a"></div>
  <div class="abs card-pay" style="left:664px;background:#5f8fc4"></div>
  <div class="abs card-pay" style="left:691px;background:#dfe6ef"></div>
  <div class="abs footer-rule"></div>
  <div class="abs copyright">Copyright © 2016, moon tot goods All Right Reserved.</div>
</footer>

<div class="abs dim"></div>

<div class="abs popup" role="dialog" aria-label="Newsletter discount offer">
  <div class="abs popup-photo" role="img" aria-label="Photo of a baby sitting with a colourful toy train"></div>
  <div class="abs popup-title">Want <strong>10%</strong> off your next order ?</div>
  <p class="abs popup-text">Suscribe to our mailing list below and get a 10% off code to use at check out.<br>If they don't want to subscribe, they have the option to select</p>
  <div class="abs btn btn-decline">NO THANK YOU I WANT TO PAY FULL PRICE</div>
  <div class="abs btn btn-subscribe">SUBSCRIBE</div>
</div>
<div class="abs close">✕</div>
</body>
</html>
```